Rollers & Glides.com

Vertical Business Card with focus on branding with our icon. Information on card will be logo, persons name, position, phone number, email address and website. Use the the name Marcus Pellow, position President, phone number 480.915.2267, email Marcus@rollersandglides-demo.com, website www.rollersandglides-demo.com.

```html
<!DOCTYPE html>
<html lang="en">
<head>
<meta charset="utf-8">
<title>Rollers &amp; Glides.com – Business Card</title>
<link href="https://fonts.googleapis.com/css2?family=Roboto+Condensed:wght@400&family=Roboto:wght@400;700&display=swap" rel="stylesheet">
<style>
  :root {
    --brand-blue: #325fab;
    --text-blue: #2f5cab;
    --ink: #222222;
    --paper: #ffffff;
    --backdrop: #e6e6e6;
  }
  * { margin: 0; padding: 0; box-sizing: border-box; }
  html, body { width: 1200px; height: 900px; overflow: hidden; }
  body { background: var(--backdrop); position: relative; font-family: "Roboto", Arial, sans-serif; }

  .card {
    position: absolute;
    top: 217px;
    width: 309px;
    height: 500px;
    overflow: hidden;
  }
  .card-front {
    left: 279px;
    background: var(--brand-blue);
    border-radius: 0 66px 0 66px;
  }
  .card-back {
    left: 617px;
    background: var(--paper);
    border-radius: 66px 0 66px 0;
  }

  .wordmark {
    font-family: "Roboto Condensed", "Arial Narrow", sans-serif;
    font-weight: 400;
    letter-spacing: 0.5px;
    white-space: nowrap;
  }
  .card-front .wordmark {
    position: absolute;
    left: 37px;
    top: 418px;
    font-size: 24px;
    color: var(--paper);
  }

  .brand-block {
    position: absolute;
    left: 0;
    right: 0;
    top: 128px;
    text-align: center;
  }
  .brand-dot {
    display: block;
    width: 52px;
    height: 52px;
    margin: 0 auto 32px;
    border-radius: 50%;
    background: var(--text-blue);
  }
  .card-back .wordmark {
    font-size: 27px;
    color: var(--text-blue);
  }

  .person {
    position: absolute;
    left: 34px;
    top: 345px;
  }
  .person-name {
    font-size: 18px;
    font-weight: 700;
    color: var(--text-blue);
    text-transform: uppercase;
    line-height: 1.1;
  }
  .person-title {
    font-size: 14px;
    color: var(--ink);
    line-height: 1.2;
  }

  .contact-list {
    position: absolute;
    left: 33px;
    top: 403px;
    list-style: none;
  }
  .contact-item {
    display: flex;
    align-items: center;
    gap: 6px;
    font-size: 14px;
    color: var(--ink);
    height: 18px;
    white-space: nowrap;
  }
  .contact-icon { width: 13px; height: 13px; flex: none; fill: var(--text-blue); }
  .accent { color: var(--text-blue); }
</style>
</head>
<body>
  <section class="card card-front" aria-label="Card front">
    <p class="wordmark">Rollers &amp; Glides.com</p>
  </section>

  <section class="card card-back" aria-label="Card back">
    <div class="brand-block">
      <span class="brand-dot" aria-hidden="true"></span>
      <p class="wordmark">Rollers &amp; Glides.com</p>
    </div>

    <div class="person">
      <p class="person-name">Marcus Pellow</p>
      <p class="person-title">President</p>
    </div>

    <ul class="contact-list">
      <li class="contact-item">
        <svg class="contact-icon" viewBox="0 0 24 24" aria-hidden="true"><path d="M6.6 10.8a15.1 15.1 0 0 0 6.6 6.6l2.2-2.2a1 1 0 0 1 1-.25 11.4 11.4 0 0 0 3.6.57 1 1 0 0 1 1 1V20a1 1 0 0 1-1 1A17 17 0 0 1 3 4a1 1 0 0 1 1-1h3.5a1 1 0 0 1 1 1c0 1.25.2 2.45.57 3.57a1 1 0 0 1-.25 1z"/></svg>
        <span>480.915.2267</span>
      </li>
      <li class="contact-item">
        <svg class="contact-icon" viewBox="0 0 24 24" aria-hidden="true"><path d="M2 5h20v14H2z M3.5 6.5 12 13l8.5-6.5" /><path d="M2 5l10 8 10-8" fill="none" stroke="#fff" stroke-width="1.5"/></svg>
        <span>Marcus@rollersandglides-demo.com</span>
      </li>
      <li class="contact-item">
        <svg class="contact-icon" viewBox="0 0 24 24" aria-hidden="true"><circle cx="12" cy="12" r="10" fill="none" stroke="#2f5cab" stroke-width="2"/><ellipse cx="12" cy="12" rx="4" ry="10" fill="none" stroke="#2f5cab" stroke-width="1.6"/><path d="M2 12h20M4 7h16M4 17h16" stroke="#2f5cab" stroke-width="1.6"/></svg>
        <span>www.<span class="accent">rollersandglides-demo</span>.com</span>
      </li>
    </ul>
  </section>
</body>
</html>
```